Quillmere Supply Chain and Logistic Consulting

Please review the attached Business Card. I want as close to this card with the colors, fonts, and quality of the card as possible. The attached compass should replace the deer head on both sides of the card and the text should say:

Backside
Compass JPEG
Quillmere SLG
A Supply Chain and Logistics Consulting Company

Frontside
Quillmere SLG
Ray Falkner - Fernport Oregon
President
____________________________________
(555) 314-9027
QuillmereSLG@Examplemail.com
_____________________________________

Bottom Front Side

Target Market(s)

Businesses

Contact Information for Business Card

Backside
Compass JPEG
Quillmere SLG

Frontside
Quillmere SLG
President
(555) 314-9027
QuillmereSLG@Examplemail.com

Bottom Front Side

Font styles to use
Serif
Script

Colors

Designer to choose colors to be used in the design.

Requirements
Must have
• See attached card for reference
Nice to have
Should not have

```html
<!DOCTYPE html>
<html lang="en">
<head>
<meta charset="utf-8">
<title>Quillmere SLG Business Card</title>
<link rel="stylesheet" href="https://fonts.googleapis.com/css2?family=Cinzel:wght@400;500&family=Cormorant+SC:wght@500&family=Tinos:wght@400;700&display=swap">
<style>
  :root {
    --backdrop: #2c2c2c;
    --card: #111111;
    --silver: #dcdcdc;
    --silver-soft: #b8b8b8;
    --tagline: #a9a9a9;
    --rule: #4a4a4a;
    --edge-dark: #5a5a5a;
    --edge-light: #f4f4f4;
  }
  * { box-sizing: border-box; margin: 0; padding: 0; }
  html, body { width: 1200px; height: 866px; overflow: hidden; }
  body {
    background: var(--backdrop);
    display: flex;
    align-items: center;
    justify-content: center;
    gap: 60px;
  }
  .card {
    position: relative;
    width: 520px;
    height: 297px;
    background: var(--card);
    color: var(--silver);
    display: flex;
    flex-direction: column;
    align-items: center;
    justify-content: center;
    text-align: center;
    box-shadow: 0 6px 0 -1px var(--edge-dark), 0 14px 28px rgba(0,0,0,.55);
  }
  .card::after {
    content: "";
    position: absolute;
    left: 0; right: 0; bottom: -6px;
    height: 5px;
    background: linear-gradient(90deg, var(--edge-dark), var(--edge-light) 40%, var(--edge-dark) 70%, var(--edge-light) 90%, var(--edge-dark));
  }
  .company-name {
    font-family: "Cinzel", serif;
    font-weight: 400;
    font-size: 36px;
    letter-spacing: 1px;
    color: var(--silver);
  }
  .front .company-name { margin-bottom: 10px; }
  .person {
    font-family: "Tinos", serif;
    font-weight: 700;
    font-size: 20px;
    color: var(--silver);
  }
  .title {
    font-family: "Tinos", serif;
    font-size: 16px;
    color: var(--silver-soft);
    margin-top: 2px;
  }
  .rule {
    width: 230px;
    height: 1px;
    background: var(--rule);
    margin: 6px 0;
  }
  .contact {
    font-family: "Tinos", serif;
    font-size: 17px;
    line-height: 1.2;
    color: var(--silver);
  }
  .tagline {
    font-family: "Cormorant SC", serif;
    font-weight: 500;
    font-size: 17px;
    letter-spacing: 1.5px;
    color: var(--tagline);
    margin-top: 8px;
  }
  .back .mark-circle {
    width: 110px;
    height: 110px;
    border-radius: 50%;
    border: 2px solid var(--silver);
    margin-bottom: 16px;
  }
  .back .company-name { font-size: 28px; }
</style>
</head>
<body>
  <section class="card front">
    <h1 class="company-name">Quillmere SLG</h1>
    <p class="person">Ray Falkner - Fernport Oregon</p>
    <p class="title">President</p>
    <div class="rule"></div>
    <p class="contact">(555) 314-9027</p>
    <p class="contact">QuillmereSLG@Examplemail.com</p>
    <div class="rule"></div>
    <p class="tagline">A Supply Chain and Logistics Consulting Company</p>
  </section>

  <section class="card back">
    <div class="mark-circle"></div>
    <p class="company-name">Quillmere SLG</p>
  </section>
</body>
</html>
```